Corvane Capital Business Cards

These are professional business cards that are for my family office.
Put fake emails and phone numbers as of now until I finalize those components. This family office controls my families investments, assets, and future. The cards should be professional.
..
.
.
.
I just uploaded another variation of a logo I would like to see as a business card to I am inbeteen which logo to use

Target Market(s)

business

Industry/Entity Type

business

Contact Information for Business Card

Professional, wealth related, finance related.

Requirements
Must have
• Logo

```html
<!DOCTYPE html>
<html lang="en">
<head>
<meta charset="utf-8">
<title>Corvane Capital Business Cards</title>
<link rel="stylesheet" href="https://fonts.googleapis.com/css2?family=Cinzel:wght@600&family=Poppins:wght@400;500;600&display=swap">
<style>
  :root {
    --page: #e3e7e8;
    --navy: #151b28;
    --navy-raised: #2b3242;
    --ring: #3c4352;
    --silver: #a9a9a9;
    --name-grey: #b4b4b4;
    --white: #ffffff;
  }
  * { margin: 0; padding: 0; box-sizing: border-box; }
  html, body { width: 1200px; height: 960px; overflow: hidden; background: var(--page); }
  .sheet { position: relative; width: 1200px; height: 960px; }
  .card {
    position: absolute; left: 250px; width: 701px; height: 400px;
    background: var(--navy); overflow: hidden;
  }
  .card--front { top: 60px; }
  .card--back { top: 500px; }

  .front-mark {
    position: absolute; left: 259px; top: 80px; width: 184px; height: 184px;
    border: 3px solid var(--ring); border-radius: 50%;
  }
  .front-name {
    position: absolute; left: 0; right: 0; top: 286px; text-align: center;
    font-family: "Cinzel", serif; font-weight: 600; font-size: 36px;
    letter-spacing: 1px; color: var(--navy-raised);
  }

  .back-name {
    position: absolute; left: 0; right: 0; top: 42px; text-align: center;
    font-family: "Cinzel", serif; font-weight: 600; font-size: 46px;
    color: var(--white); letter-spacing: 1px;
  }
  .person { position: absolute; right: 388px; top: 208px; text-align: right; font-family: "Poppins", sans-serif; }
  .person__name { font-size: 32px; line-height: 40px; color: var(--name-grey); font-weight: 400; white-space: nowrap; }
  .person__name strong { font-weight: 600; }
  .person__title { font-size: 17px; line-height: 22px; color: var(--white); font-weight: 500; letter-spacing: .5px; }
  .divider { position: absolute; left: 350px; top: 196px; width: 2px; height: 104px; background: var(--white); }
  .contacts { position: absolute; left: 384px; top: 212px; list-style: none; font-family: "Poppins", sans-serif; }
  .contacts li { display: flex; align-items: center; height: 26px; font-size: 19px; color: var(--white); letter-spacing: .4px; }
  .contacts svg { width: 18px; height: 18px; margin-right: 13px; flex: none; }
  .band { position: absolute; left: 0; top: 0; width: 701px; height: 400px; }
  .address {
    position: absolute; left: 0; right: 0; top: 356px; text-align: center;
    font-family: "Poppins", sans-serif; font-size: 18px; color: var(--white); letter-spacing: .3px;
  }
</style>
</head>
<body>
<main class="sheet">
  <section class="card card--front" aria-label="Card front">
    <div class="front-mark"></div>
    <p class="front-name">CORVANE CAPITAL</p>
  </section>

  <section class="card card--back" aria-label="Card back">
    <svg class="band" viewBox="0 0 701 400" aria-hidden="true">
      <path d="M0 281 Q351 410 701 281 V400 H0 Z" fill="var(--silver)"/>
      <path d="M25 282 Q351 372 676 282 Q351 352 25 282 Z" fill="var(--white)"/>
    </svg>
    <p class="back-name">CORVANE CAPITAL</p>
    <div class="person">
      <p class="person__name"><strong>Marta</strong> Delacourt</p>
      <p class="person__title">Founder &amp; CEO</p>
    </div>
    <div class="divider"></div>
    <ul class="contacts">
      <li>
        <svg viewBox="0 0 24 24" aria-hidden="true"><path d="M6.6 3.5l3 3.2-1.7 2.4c1 2.2 2.8 4 5 5l2.4-1.7 3.2 3-1.8 3.1C10.5 18.2 5.8 13.5 3.5 5.3z" fill="none" stroke="#d0d0d0" stroke-width="1.8" stroke-linejoin="round"/></svg>
        (555) 014-2290
      </li>
      <li>
        <svg viewBox="0 0 24 24" aria-hidden="true"><circle cx="12" cy="12" r="9" fill="none" stroke="#d0d0d0" stroke-width="1.8"/><path d="M3 12h18M12 3c3 3 3 15 0 18M12 3c-3 3-3 15 0 18" fill="none" stroke="#d0d0d0" stroke-width="1.4"/></svg>
        info@yourwebsite.com
      </li>
      <li>
        <svg viewBox="0 0 24 24" aria-hidden="true"><rect x="2.5" y="6" width="19" height="13" fill="none" stroke="#d0d0d0" stroke-width="1.8"/><path d="M2.5 6l9.5 7 9.5-7" fill="none" stroke="#d0d0d0" stroke-width="1.6"/></svg>
        www.yourwebsite.com
      </li>
    </ul>
    <p class="address">4180 Linden Ave. Suite 310 Harlow Ridge, TX 75590</p>
  </section>
</main>
</body>
</html>
```